IV Nutritional Clinic Web Design

We are working with Velqo. They are an IV Nutritional Clinic and in need of a new website design.
Some sites to use for inspiration:
https://brightpathcareco.com
https://www.ourzavrowellness.com
https://www.dewspringlounge.com
https://qvitalsurge.com
https://www.lumo-vital.com/pages/iv-therapy-west-hollywood
https://www.tqoncologyhub.com/cancer-care/iv-drips/
https://dripwellary.com
https://corvinahealthhub.com
Thank you for taking the time to consider designing a website for us. We are web developers based in Stockton, CA, USA. Most of our projects go through the same process. Understanding this process may help you win a project with us. We custom-code all of our websites in-house. We don’t have any requirements as to what tools you use for your design, but we prefer Figma files. For any design that we label as four-stars, we send it to the client for review. The client picks the final design they want us to use. Once we complete this process, we will continue to show additional clients all the four-star sites and purchase them later. Your designs will have multiple chances to sell. For better chances of success, we ask that you follow these guidelines.
IMAGES:
If you use any images or icons in the design, we ask that you have a link to the asset so we can purchase the image/icon. Most of the designs we submit do not have the customer’s images on them unless they have some great images. Be creative; show us the feeling you are trying to portray with your image choices. Use any royalty-free site you choose. We subscribe to Pixvane and mainly use their images, but we can purchase images outside of Pixvane.
PLEASE NOTE: we will not submit designs to clients with watermarks on the images.
FONTS:
We ask that you identify the fonts used in the design. This can be done in a message if you want. We typically use Google Fonts and Pixvane Fonts.
CONTENT:
We're always open to different content and ideas. We often submit designs with stock images so the client can see our vision. We typically take pictures after the website launch to use their images with our vision. Lorem Ipsum is fine for paragraphs, but we ask that you write the headers in correct English. We want to be able to show the vision and identify the sections of the website.
INSPIRATION:
We typically add a couple of links in the brief of websites we like to help you get started in your design.
REVISIONS:
We do not often ask for revisions of the designs unless we see something in the design that may not appeal to the client. If there are slight changes that we want to make, we do that in the development process.
FEEDBACK:
We rarely give feedback on designs during the design process. We are working on many website projects and do not have the time to provide feedback. We usually respond if your request is well thought out and asks specific questions, but a note asking “feedback, please” usually goes unanswered.

```html
<!DOCTYPE html>
<html lang="en">
<head>
<meta charset="utf-8">
<title>Velqo Hydration – IV Nutritional Clinic</title>
<link rel="stylesheet" href="https://fonts.googleapis.com/css2?family=Poppins:wght@400;500;600;700;800&display=swap">
<style>
:root{
  --navy:#161a7c;
  --green:#659a2e;
  --green-dark:#56882a;
  --green-bg:#6aa33a;
  --ink:#222;
  --text:#555;
  --light:#f1f1f1;
  --dark:#2a2a2a;
  --white:#fff;
}
*{box-sizing:border-box;margin:0;padding:0}
html,body{width:1200px;height:4804px;overflow:hidden}
body{font-family:"Poppins",sans-serif;color:var(--ink);background:var(--white)}
.canvas{position:relative;width:1200px;height:4804px;overflow:hidden}
.abs{position:absolute}
.btn{position:absolute;display:flex;align-items:center;justify-content:center;background:var(--green);color:#fff;border-radius:30px;font-weight:700;font-size:13px;text-transform:uppercase;letter-spacing:.2px}
.rule{position:absolute;height:3px;width:56px;background:var(--green)}
.photo{position:absolute}
p{line-height:1.75}

/* header */
.site-header{position:absolute;left:0;top:0;width:1200px;height:86px;background:#fff}
.brand{position:absolute;left:103px;top:14px;font-weight:800;font-size:38px;letter-spacing:2px;color:var(--navy);text-transform:uppercase}
.menu-icon{position:absolute;left:864px;top:35px}

/* hero */
.hero{position:absolute;left:0;top:86px;width:1200px;height:571px;background:linear-gradient(90deg,#cfcac2 0%,#ebe8e3 30%,#dcd6cd 60%,#b9b1a6 100%)}
.hero h1{position:absolute;left:0;top:194px;width:1200px;text-align:center;color:#fff;font-weight:800;font-size:58px;line-height:66px;text-transform:uppercase}
.dot{position:absolute;width:24px;height:24px;border-radius:50%;display:flex;align-items:center;justify-content:center;font-size:12px}

/* about */
.about-frame{position:absolute;background:#fff;box-shadow:0 4px 14px rgba(0,0,0,.25);padding:6px}
.about-frame div{width:100%;height:100%}
.h2{position:absolute;font-weight:800;font-size:30px;color:var(--navy);text-transform:uppercase}
.body-text{position:absolute;font-size:13.5px;color:var(--text)}

/* why */
.why{position:absolute;left:0;top:1217px;width:1200px;height:412px;background:var(--navy)}
.video{position:absolute;left:146px;top:1426px;width:908px;height:403px;background:#fff;padding:5px;box-shadow:0 10px 28px rgba(0,0,0,.3)}

/* services */
.service{position:absolute;top:2043px;width:240px;height:271px;border-radius:8px;overflow:hidden;background:#333}
.service .img{height:207px}
.service .label{height:64px;display:flex;align-items:center;justify-content:center;color:#fff;font-weight:600;font-size:16px}
.service.active .label{background:var(--green)}

/* testimonials */
.testi-bg{position:absolute;left:0;top:2487px;width:1200px;height:586px;background:var(--light)}
.testi{position:absolute;top:2726px;width:495px;height:237px;background:#fff}
.testi.shadow{box-shadow:0 4px 16px rgba(0,0,0,.12)}
.testi.outline{border:1px solid #555}
.avatar{position:absolute;left:22px;top:18px;width:90px;height:90px;border-radius:50%}
.testi .name{position:absolute;left:130px;top:26px;color:var(--green);font-weight:700;font-size:17px}
.testi .role{position:absolute;left:130px;top:50px;font-size:13px;color:#444}
.testi .quote{position:absolute;left:130px;top:78px;width:300px;font-size:12.5px;line-height:22px;color:#555}
.testi .more{position:absolute;left:130px;top:190px;font-size:13px;font-weight:600;color:var(--green);text-decoration:underline}
.testi .stars{position:absolute;left:376px;top:186px;color:#9a8a10;font-size:16px;letter-spacing:1px}

/* news */
.news-bg{position:absolute;left:0;top:3073px;width:1200px;height:715px;background:radial-gradient(ellipse at 40% 40%,#78b244 0%,#64a034 55%,#57912c 100%)}
.news{position:absolute;top:3247px;width:293px;height:414px;background:#fff;border-radius:10px;padding:7px}
.news .img{height:250px;border-radius:6px}
.news .date{margin:20px 0 0 9px;color:var(--navy);font-weight:700;font-size:15px}
.news .title{margin:10px 0 0 9px;font-weight:700;font-size:16.5px;line-height:28px;color:#222}

/* contact */
.contact-bg{position:absolute;left:0;top:3788px;width:1200px;height:597px;background:linear-gradient(180deg,#fff 0%,#f3f3f3 100%)}
.c-icon{position:absolute;left:131px;width:66px;height:66px;border-radius:50%;background:#fff;box-shadow:0 3px 12px rgba(0,0,0,.14);display:flex;align-items:center;justify-content:center}
.c-label{position:absolute;left:222px;font-weight:700;font-size:20px}
.c-text{position:absolute;left:222px;font-size:13.5px;line-height:24px;color:#444}
.field{position:absolute;background:#fff;border:1px solid #ddd;font-size:13.5px;color:#666;padding:13px 14px}

/* footer */
.site-footer{position:absolute;left:0;top:4385px;width:1200px;height:419px;background:var(--dark);color:#fff}
.f-brand{position:absolute;left:103px;top:68px;font-weight:800;font-size:54px;letter-spacing:4px;color:#fff;text-transform:uppercase}
.f-h{position:absolute;top:70px;font-weight:600;font-size:23px}
.f-links{position:absolute;left:348px;top:118px;font-size:14px;line-height:30px}
.f-icon{position:absolute;left:549px;width:46px;height:46px;border-radius:50%;background:#fff;display:flex;align-items:center;justify-content:center}
.f-ct{position:absolute;left:609px;font-size:11.5px;line-height:20px}
.f-ct b{font-size:14px}
.newsletter{position:absolute;left:843px;top:114px;width:280px;height:47px;background:#fff;border-radius:24px;overflow:hidden}
.newsletter span{position:absolute;left:20px;top:14px;font-size:13.5px;font-weight:500;color:#222}
.newsletter i{position:absolute;right:0;top:0;width:50px;height:47px;background:var(--green);display:flex;align-items:center;justify-content:center}
.social{position:absolute;top:4770px;width:22px;height:22px;border-radius:50%;background:var(--green)}
</style>
</head>
<body>
<div class="canvas">

  <!-- header -->
  <header class="site-header">
    <div class="brand">Velqo</div>
    <svg class="menu-icon" width="18" height="14" viewBox="0 0 18 14"><rect width="18" height="2.4" fill="#333"/><rect y="5.8" width="18" height="2.4" fill="#333"/><rect y="11.6" width="18" height="2.4" fill="#333"/></svg>
    <div class="btn" style="left:905px;top:21px;width:190px;height:42px;font-size:13px">Free Consultation</div>
  </header>

  <!-- hero -->
  <section class="hero">
    <div class="photo" role="img" aria-label="Two clients in white robes relaxing in armchairs during IV therapy" style="inset:0;background:inherit"></div>
    <h1>Welcome to your<br>healthy place.</h1>
    <div class="btn" style="left:532px;top:356px;width:134px;height:39px">Book Now</div>
    <div class="dot" style="left:565px;top:510px;background:#fff;color:#333">‹</div>
    <div class="dot" style="left:609px;top:510px;background:#fff;color:#333">›</div>
  </section>

  <!-- about -->
  <section>
    <div class="about-frame" style="left:103px;top:735px;width:348px;height:296px"><div role="img" aria-label="Client in robe relaxing in a bright lounge" style="background:linear-gradient(135deg,#e9e6e0,#cfc7bc)"></div></div>
    <div class="about-frame" style="left:308px;top:867px;width:252px;height:268px"><div role="img" aria-label="Nurse attending a patient receiving an IV drip" style="background:linear-gradient(135deg,#d8d4cc,#8ea0b8)"></div></div>
    <div class="h2" style="left:642px;top:781px">About Velqo Hydration</div>
    <div class="rule" style="left:642px;top:828px"></div>
    <p class="body-text" style="left:642px;top:847px;width:430px">Lorem ipsum dolor sit amet, consectetur adipiscing elit, sed do eiusmod tempor incididunt ut labore et dolore magna aliqua. Quis ipsum suspendisse ultrices gravida.</p>
    <p class="body-text" style="left:642px;top:926px;width:430px">Sed ut perspiciatis unde omnis iste natus error sit voluptatem accusantium doloremque laudantium, totam rem aperiam, eaque ipsa quae ab illo inventore veritatis et quasi architecto beatae vitae dicta sunt explicabo.</p>
    <div class="btn" style="left:642px;top:1039px;width:133px;height:40px">Read More</div>
  </section>

  <!-- why choose us -->
  <section class="why">
    <div class="h2" style="left:0;top:53px;width:1200px;text-align:center;color:#fff;font-size:29px">Why Choose Us</div>
    <div class="rule" style="left:572px;top:99px"></div>
    <p class="abs" style="left:100px;top:124px;width:1000px;text-align:center;color:#fff;font-size:13.5px;line-height:26px">Lorem ipsum dolor sit amet, consectetur adipiscing elit, sed do eiusmod tempor incididunt ut labore et dolore magna aliqua.<br>Quis ipsum suspendisse ultrices gravida. Risus commodo viverra maecenas accumsan lacus vel facilisis.</p>
  </section>
  <div class="video">
    <div role="img" aria-label="Nurse preparing an IV line for a seated patient" style="width:100%;height:100%;background:linear-gradient(120deg,#6f7680 0%,#a7b0bc 45%,#8c96a6 70%,#4c5460 100%);position:relative">
      <svg style="position:absolute;left:427px;top:171px" width="44" height="44" viewBox="0 0 44 44"><circle cx="22" cy="22" r="22" fill="#fff"/><path d="M17 13 L32 22 L17 31Z" fill="var(--navy)"/></svg>
    </div>
  </div>

  <!-- services -->
  <section>
    <div class="h2" style="left:0;top:1900px;width:1200px;text-align:center;font-size:29px">Our Comprehensive Wellness Services</div>
    <div class="rule" style="left:572px;top:1946px"></div>
    <p class="abs" style="left:150px;top:1965px;width:900px;text-align:center;font-size:13.5px;line-height:25px;color:#444">Lorem ipsum dolor sit amet, consectetur adipiscing elit, sed do eiusmod tempor incididunt ut labore et dolore magna aliqua. Quis ipsum suspendisse ultrices gravida. Risus commodo viverra maecenas accumsan lacus vel facilisis.</p>
    <div class="service" style="left:103px"><div class="img" role="img" aria-label="Woman measuring her waist" style="background:linear-gradient(160deg,#f1f1f1,#c9c6c2)"></div><div class="label">Weight Loss</div></div>
    <div class="service active" style="left:355px"><div class="img" role="img" aria-label="Close-up of smooth skin and lips" style="background:linear-gradient(160deg,#e2c6b4,#b98c78)"></div><div class="label">Peptide Therapy</div></div>
    <div class="service" style="left:605px"><div class="img" role="img" aria-label="Woman relaxing among green leaves" style="background:linear-gradient(160deg,#3f8c5c,#8fbf9a)"></div><div class="label">Rejuvenating Medicine</div></div>
    <div class="service" style="left:857px"><div class="img" role="img" aria-label="Patient resting with an IV drip bag" style="background:linear-gradient(160deg,#b7c4d6,#5b7394)"></div><div class="label">IV Therapy</div></div>
    <div class="dot" style="left:565px;top:2354px;background:var(--navy);color:#fff">‹</div>
    <div class="dot" style="left:609px;top:2354px;background:#eee;color:#555">›</div>
  </section>

  <!-- testimonials -->
  <section class="testi-bg"></section>
  <div class="h2" style="left:103px;top:2593px;font-size:29px">Client’s Testimonials</div>
  <div class="rule" style="left:103px;top:2639px"></div>
  <p class="abs" style="left:103px;top:2657px;width:640px;font-size:13.5px;line-height:25px;color:#444">Lorem ipsum dolor sit amet, consectetur adipiscing elit, sed do eiusmod tempor incididunt ut labore et dolore magna aliqua.</p>
  <div class="dot" style="left:1036px;top:2600px;background:var(--green);color:#fff;width:28px;height:28px">‹</div>
  <div class="dot" style="left:1080px;top:2600px;background:#fff;color:#555;width:28px;height:28px;border:1px solid #ccc">›</div>

  <div class="testi shadow" style="left:95px">
    <div class="avatar" role="img" aria-label="Portrait of Alex" style="background:linear-gradient(135deg,#e9c98c,#8a6a4c)"></div>
    <div class="name">Alex</div><div class="role">Patient</div>
    <div class="quote">Lorem ipsum dolor sit amet, consectetur adipiscing elit, sed do eiusmod tempor incididunt ut labore et dolore magna Ut enim ad aliqua.</div>
    <div class="more">Read More</div><div class="stars">★★★★★</div>
  </div>
  <div class="testi outline" style="left:610px">
    <div class="avatar" role="img" aria-label="Portrait of Martines" style="background:linear-gradient(135deg,#dfe3e8,#7d8795)"></div>
    <div class="name">Martines</div><div class="role">Patient</div>
    <div class="quote">Lorem ipsum dolor sit amet, consectetur adipiscing elit, sed do eiusmod tempor incididunt ut labore et dolore magna Ut enim ad aliqua.</div>
    <div class="more">Read More</div><div class="stars">★★★★★</div>
  </div>

  <!-- news -->
  <section class="news-bg"></section>
  <div class="h2" style="left:0;top:3153px;width:1200px;text-align:center;color:#fff;font-size:29px">Latest News</div>
  <div class="rule" style="left:572px;top:3199px;background:#fff"></div>
  <article class="news" style="left:131px"><div class="img" role="img" aria-label="Smiling couple embracing" style="background:linear-gradient(135deg,#8fa3b8,#5a4a3e)"></div><div class="date">03-10-2023</div><div class="title">Lorem ipsum dolor sit amet, consectetur adipiscing elit, sed do eiusmod</div></article>
  <article class="news" style="left:453px"><div class="img" role="img" aria-label="Nurse setting up an IV drip for a patient" style="background:linear-gradient(135deg,#6d7580,#a9b3bf)"></div><div class="date">03-10-2023</div><div class="title">Lorem ipsum dolor sit amet, consectetur adipiscing elit, sed do eiusmod</div></article>
  <article class="news" style="left:778px"><div class="img" role="img" aria-label="Confident woman in a modern clinic" style="background:linear-gradient(135deg,#d9dde2,#8a2a34)"></div><div class="date">03-10-2023</div><div class="title">Lorem ipsum dolor sit amet, consectetur adipiscing elit, sed do eiusmod</div></article>

  <!-- contact -->
  <section class="contact-bg"></section>
  <div class="h2" style="left:0;top:3862px;width:1200px;text-align:center;font-size:29px">Contact Us</div>
  <div class="rule" style="left:572px;top:3908px"></div>

  <div class="c-icon" style="top:3990px"><svg width="20" height="24" viewBox="0 0 20 24"><path d="M10 0C4.5 0 0 4.3 0 9.6 0 16.8 10 24 10 24s10-7.2 10-14.4C20 4.3 15.5 0 10 0z" fill="var(--navy)"/><circle cx="10" cy="9.5" r="3.6" fill="#fff"/></svg></div>
  <div class="c-label" style="top:3976px">Location :</div>
  <div class="c-text" style="top:4010px">25,Psyiq Lorem ipsum dolor<br>Sed ut perspiciatis 250</div>

  <div class="c-icon" style="top:4091px"><svg width="20" height="20" viewBox="0 0 24 24"><path d="M6.6 10.8a15.1 15.1 0 006.6 6.6l2.2-2.2c.3-.3.7-.4 1-.2 1.1.4 2.3.6 3.6.6.6 0 1 .4 1 1V20c0 .6-.4 1-1 1A17 17 0 013 4c0-.6.4-1 1-1h3.5c.6 0 1 .4 1 1 0 1.3.2 2.5.6 3.6.1.3 0 .7-.2 1z" fill="var(--navy)"/></svg></div>
  <div class="c-label" style="top:4096px">Phone:</div>
  <div class="c-text" style="top:4130px">+1 888 888 8888</div>

  <div class="c-icon" style="top:4192px"><svg width="22" height="16" viewBox="0 0 22 16"><rect width="22" height="16" rx="2" fill="var(--navy)"/><path d="M1 1.5 L11 9 L21 1.5" stroke="#fff" stroke-width="1.8" fill="none"/></svg></div>
  <div class="c-label" style="top:4197px">Email :</div>
  <div class="c-text" style="top:4231px">info@velqohydration.com</div>

  <div class="field" style="left:599px;top:3980px;width:246px;height:54px">First Name</div>
  <div class="field" style="left:859px;top:3980px;width:246px;height:54px">Last Name</div>
  <div class="field" style="left:599px;top:4053px;width:246px;height:56px">Phone</div>
  <div class="field" style="left:859px;top:4053px;width:246px;height:56px">Email</div>
  <div class="field" style="left:599px;top:4126px;width:506px;height:117px">Mesage</div>
  <div class="btn" style="left:599px;top:4258px;width:106px;height:39px">Submit</div>

  <!-- footer -->
  <footer class="site-footer">
    <div class="f-brand">Velqo</div>
    <div class="f-h" style="left:345px">Quick Links</div>
    <div class="f-links">Home<br>About Us<br>Services<br>Video<br>Contact Us</div>

    <div class="f-h" style="left:549px">Contact Us</div>
    <div class="f-icon" style="top:112px"><svg width="14" height="18" viewBox="0 0 20 24"><path d="M10 0C4.5 0 0 4.3 0 9.6 0 16.8 10 24 10 24s10-7.2 10-14.4C20 4.3 15.5 0 10 0z" fill="var(--green)"/><circle cx="10" cy="9.5" r="3.6" fill="#fff"/></svg></div>
    <div class="f-ct" style="top:112px"><b>Location :</b><br>25,velqohydration Lorem<br>Sed ut perspiciatis 250</div>
    <div class="f-icon" style="top:190px"><svg width="16" height="16" viewBox="0 0 24 24"><path d="M6.6 10.8a15.1 15.1 0 006.6 6.6l2.2-2.2c.3-.3.7-.4 1-.2 1.1.4 2.3.6 3.6.6.6 0 1 .4 1 1V20c0 .6-.4 1-1 1A17 17 0 013 4c0-.6.4-1 1-1h3.5c.6 0 1 .4 1 1 0 1.3.2 2.5.6 3.6.1.3 0 .7-.2 1z" fill="var(--green)"/></svg></div>
    <div class="f-ct" style="top:190px"><b>Phone:</b><br>+1 888 888 8888</div>
    <div class="f-icon" style="top:264px"><svg width="18" height="13" viewBox="0 0 22 16"><rect width="22" height="16" rx="2" fill="var(--green)"/><path d="M1 1.5 L11 9 L21 1.5" stroke="#fff" stroke-width="1.8" fill="none"/></svg></div>
    <div class="f-ct" style="top:264px"><b>Email :</b><br>info@velqohydration.com</div>

    <div class="f-h" style="left:843px">Newsletter</div>
    <div class="newsletter"><span>Enter Email</span><i><svg width="16" height="16" viewBox="0 0 24 24"><path d="M2 11 L22 2 L15 22 L11 13Z" fill="#fff"/></svg></i></div>

    <div class="abs" style="left:30px;top:345px;width:1140px;height:1px;background:#5a5a5a"></div>
    <div class="abs" style="left:0;top:378px;width:1200px;text-align:center;font-size:13.5px">Copyright © Velqo Hydration 2025 | All Rights Reserved</div>
  </footer>
  <div class="social" style="left:33px"></div>
  <div class="social" style="left:69px"></div>
  <div class="social" style="left:105px"></div>

</div>
</body>
</html>
```